Corvane Freight Company Business Card Design

We are a company that delivers natural saltwater (from the ocean) to aquarium companies, restaurants and home marine tanks. I would like a new business card to suit.

Must include Name, company name, abn, contact number and website as well as logo (see attached).

Looking for a design that stands out, has a clean but unique appearance.

Double and single sided entries welcome

Business

• Logo

```html
<!DOCTYPE html>
<html lang="en">
<head>
<meta charset="utf-8">
<title>Corvane Freight Company – Business Card</title>
<link rel="stylesheet" href="https://fonts.googleapis.com/css2?family=Source+Sans+3:wght@400;600;700&display=swap">
<style>
  :root {
    --stage: #0e0e0f;
    --card: #ffffff;
    --brand-blue: #1a8fd0;
    --deep-blue: #0a5fab;
    --band-blue: #0aa0d8;
    --ink: #1b1b1b;
    --contact-ink: #17528f;
  }
  * { margin: 0; padding: 0; box-sizing: border-box; }
  html, body {
    width: 1200px; height: 420px; overflow: hidden;
    background: var(--stage);
    font-family: "Source Sans 3", "Myriad Pro", sans-serif;
  }
  .stage { position: relative; width: 1200px; height: 420px; }
  .card {
    position: absolute; top: 62px; width: 516px; height: 296px;
    background: var(--card); border-radius: 22px; overflow: hidden;
  }
  .card--front { left: 67px; }
  .card--back { left: 618px; }

  .front-band { position: absolute; left: 0; bottom: 0; width: 475px; height: 110px; }
  .edge-strip {
    position: absolute; top: 0; right: 0; width: 40px; height: 100%;
    background: var(--deep-blue);
  }

  .company-name {
    position: absolute; left: 0; color: var(--brand-blue);
    font-weight: 400; text-align: center; white-space: nowrap; letter-spacing: -0.5px;
  }
  .card--front .company-name { top: 78px; width: 475px; font-size: 35px; }
  .card--back .company-name { top: 136px; width: 516px; font-size: 41px; }

  .holder {
    position: absolute; top: 166px; left: 0; width: 475px; text-align: center;
    font-size: 17px; color: var(--ink);
  }
  .holder strong { font-weight: 700; }

  .contact {
    position: absolute; left: 0; width: 475px; text-align: center;
    font-size: 13px; color: var(--contact-ink);
  }
  .contact--line { top: 222px; display: flex; justify-content: center; gap: 22px; }
  .contact--address { top: 251px; }
  .contact--abn { top: 270px; }
  .contact-item { display: inline-flex; align-items: center; gap: 6px; }
  .contact-item svg { width: 11px; height: 11px; }
</style>
</head>
<body>
<main class="stage">
  <section class="card card--front">
    <svg class="front-band" viewBox="0 0 475 110" preserveAspectRatio="none" aria-hidden="true">
      <defs>
        <linearGradient id="bandFade" x1="0" y1="0" x2="1" y2="0">
          <stop offset="0" stop-color="#ffffff"/>
          <stop offset="0.45" stop-color="#7fcbec"/>
          <stop offset="1" stop-color="var(--band-blue)"/>
        </linearGradient>
      </defs>
      <path d="M0 44 Q200 -8 475 6 L475 110 L0 110 Z" fill="url(#bandFade)"/>
    </svg>
    <div class="edge-strip"></div>

    <h1 class="company-name">Corvane Freight Company</h1>
    <p class="holder"><strong>Your Name,</strong> Title</p>

    <div class="contact contact--line">
      <span class="contact-item">
        <svg viewBox="0 0 12 12" aria-hidden="true"><circle cx="6" cy="6" r="5.2" fill="none" stroke="currentColor" stroke-width="1"/><path d="M4 3.2 L5.2 4.6 L4.6 5.4 Q5.4 7 6.8 7.6 L7.6 7 L8.8 8.2 L8 9 Q5 8.6 3.3 4 Z" fill="currentColor"/></svg>
        123-456-7892
      </span>
      <span class="contact-item">
        <svg viewBox="0 0 12 12" aria-hidden="true"><g fill="none" stroke="currentColor" stroke-width="1"><circle cx="6" cy="6" r="5"/><ellipse cx="6" cy="6" rx="2.2" ry="5"/><path d="M1 6 H11 M2 3.5 H10 M2 8.5 H10"/></g></svg>
        www.corvanefreight.com
      </span>
    </div>
    <p class="contact contact--address">Street Name, City Name ,State, Zip Code</p>
    <p class="contact contact--abn">ABN: 123456789</p>
  </section>

  <section class="card card--back">
    <h2 class="company-name">Corvane Freight Company</h2>
  </section>
</main>
</body>
</html>
```